Canadian company needs a packaging design for a new product line of TubGlow Hot Tub & Bath Fragran

We are looking for a packaging design for a new company based in Edmonton, Alberta Canada called TubGlow. We are developing a new product line of liquid and crystal Hot Tub & Bath Fragrances (aromatherapy) for example Lavender will be one of our fragrances. We are looking at the possibilities of using a stand up pouch and or the standard plastic bottles for our fragrance line. There will be different sizes from 150 grams to 600 grams in the crystal and 275 ml in the liquid. We would like to see bright multi-colored designs possibly with picture of the fragrance or a theme like favorite drinks or a more sensual idea. Each one of our fragrances will be a different color the main design needs to be able to have a different color of liquid or crystal in the bottle and possibly parts of the label will change colors for each fragrance. I have attached samples of another brand that we want to improve on.

Target Market(s)

Most of these fragrance are bought by women 70% men 30%
age 25 - 55

Industry/Entity Type

It Company

Requirements
Must have
• bottle size
Fragrance name
Nice to have
• Using the files below I like the circle of colors and possibly it could be made using water drops like in the file and possibly the two "S" could be designed like the third file I just added

Files

```html
<!DOCTYPE html>
<html lang="en">
<head>
<meta charset="utf-8">
<title>TubGlow Packaging – Lavender Tube &amp; Ocean Reverie Pouch</title>
<link rel="stylesheet" href="https://fonts.googleapis.com/css2?family=Nunito:wght@400;800&family=Great+Vibes&family=Roboto:wght@400;500&family=Nunito+Sans:wght@300&display=swap">
<style>
  :root {
    --page-bg: #e4e4e7;
    --tube-light: #b3aee8;
    --tube-mid: #9a94d8;
    --tube-dark: #7f78c4;
    --tube-panel: #6f66c9;
    --tube-box: #7d74d4;
    --tube-box-edge: #5a51b8;
    --aqua: #4fe3ee;
    --white: #ffffff;
    --coral-violet: #c8a2e8;
    --coral-yellow: #f2dc4a;
    --pouch-sky: #d9e8f8;
    --pouch-blue: #a9cdf0;
    --pouch-deep: #2f46b8;
    --pouch-navy: #1e2f8f;
    --pouch-title: #27a8e6;
    --pouch-name: #2b3aa3;
    --text-dark: #1b1b2a;
    --reef-green: #6ab04c;
    --reef-orange: #f07a2a;
  }
  html, body {
    margin: 0;
    width: 1200px;
    height: 1042px;
    overflow: hidden;
    background: var(--page-bg);
  }
  .canvas { position: relative; width: 1200px; height: 1042px; }

  /* ---------- Lavender tube ---------- */
  .tube {
    position: absolute;
    left: 227px; top: 81px;
    width: 271px; height: 778px;
  }
  .tube-crimp {
    position: absolute; left: 0; top: 0; width: 271px; height: 18px;
    background: linear-gradient(90deg, var(--tube-dark), var(--tube-light) 40%, var(--tube-mid));
    border-radius: 4px 4px 0 0;
  }
  .tube-body {
    position: absolute; left: 0; top: 18px; width: 271px; height: 651px;
    background: linear-gradient(90deg, var(--tube-dark) 0%, var(--tube-light) 35%, var(--tube-mid) 70%, var(--tube-dark) 100%);
    overflow: hidden;
  }
  .tube-cap {
    position: absolute; left: 37px; top: 671px; width: 206px; height: 107px;
    background: linear-gradient(90deg, var(--tube-dark), var(--tube-light) 40%, var(--tube-mid) 75%, var(--tube-dark));
    border-radius: 6px 6px 10px 10px;
  }
  .tube-brand {
    position: absolute; left: 0; top: 126px; width: 271px;
    display: flex; justify-content: center; align-items: center; gap: 8px;
    font-family: "Nunito", sans-serif; font-weight: 800; font-size: 24px; line-height: 1;
    color: var(--aqua);
  }
  .brand-dot { width: 14px; height: 14px; border-radius: 50%; background: var(--aqua); }
  .tube-namebox {
    position: absolute; left: 43px; top: 190px; width: 187px; height: 65px;
    background: var(--tube-box);
    border: 2px solid var(--tube-box-edge);
    box-shadow: inset 0 0 0 4px rgba(255,255,255,0.12);
    display: flex; align-items: center; justify-content: center;
    font-family: "Nunito", sans-serif; font-weight: 400; font-size: 32px;
    color: var(--aqua);
  }
  .tube-fragrance {
    position: absolute; left: 0; top: 262px; width: 271px; text-align: center;
    font-family: "Great Vibes", cursive; font-size: 64px; line-height: 1; color: var(--white);
    -webkit-text-stroke: 1px var(--tube-box-edge);
  }
  .tube-swoosh { position: absolute; left: 0; top: 410px; width: 271px; height: 241px; }
  .tube-coral {
    position: absolute; left: 51px; top: 352px; width: 179px; height: 203px;
    background: radial-gradient(ellipse at 50% 40%, var(--coral-violet) 0%, rgba(200,162,232,0.7) 45%, rgba(242,220,74,0.35) 70%, transparent 75%);
  }
  .tube-volume {
    position: absolute; right: 16px; top: 548px; text-align: left;
    font-family: "Roboto", sans-serif; color: var(--white);
  }
  .tube-volume .ml { font-size: 23px; font-weight: 500; display: block; line-height: 1; }
  .tube-volume .wt { font-size: 10px; display: block; margin-top: 2px; }

  /* ---------- Ocean Reverie pouch ---------- */
  .pouch {
    position: absolute; left: 706px; top: 67px;
    width: 336px; height: 761px;
  }
  .pouch-seal {
    position: absolute; left: 0; top: 0; width: 336px; height: 14px;
    background: var(--pouch-deep);
  }
  .pouch-body {
    position: absolute; left: 0; top: 12px; width: 336px; height: 749px;
    background: linear-gradient(180deg, var(--pouch-blue) 0%, var(--pouch-sky) 40%, var(--pouch-sky) 70%, var(--pouch-blue) 100%);
    overflow: hidden;
  }
  .pouch-brand {
    position: absolute; left: 0; top: 125px; width: 336px;
    display: flex; justify-content: center; align-items: center; gap: 10px;
    font-family: "Nunito", sans-serif; font-weight: 800; font-size: 39px; line-height: 1.1;
    color: var(--pouch-name);
  }
  .pouch-brand .brand-dot { width: 18px; height: 18px; background: var(--pouch-name); }
  .pouch-fragrance {
    position: absolute; left: 0; top: 214px; width: 336px; text-align: center;
    font-family: "Nunito Sans", sans-serif; font-weight: 300; font-size: 44px; line-height: 1.1;
    color: var(--pouch-title); white-space: nowrap;
  }
  .pouch-rule { position: absolute; left: 38px; top: 274px; width: 260px; height: 6px; }
  .pouch-scene {
    position: absolute; left: 0; top: 315px; width: 336px; height: 289px;
    background:
      radial-gradient(ellipse at 20% 60%, rgba(200,162,232,0.9) 0%, transparent 35%),
      radial-gradient(ellipse at 85% 55%, rgba(106,176,76,0.85) 0%, transparent 35%),
      radial-gradient(ellipse at 75% 80%, rgba(240,122,42,0.8) 0%, transparent 20%),
      radial-gradient(ellipse at 45% 70%, rgba(47,70,184,0.7) 0%, transparent 30%),
      linear-gradient(180deg, transparent 0%, rgba(169,205,240,0.4) 100%);
  }
  .pouch-volume {
    position: absolute; left: 0; top: 612px; width: 336px; text-align: center;
    font-family: "Roboto", sans-serif; font-size: 17px; line-height: 20px; color: var(--text-dark);
  }
  .pouch-volume .ml { font-weight: 500; margin-right: 6px; }
  .pouch-band { position: absolute; left: 0; top: 619px; width: 336px; height: 130px; }
</style>
</head>
<body>
<main class="canvas">

  <section class="tube" aria-label="Lavender fragrance tube">
    <div class="tube-crimp"></div>
    <div class="tube-body">
      <div class="tube-brand"><span class="brand-dot"></span>TubGlow</div>
      <div class="tube-namebox">TubGlow</div>
      <div class="tube-fragrance">Lavender</div>
      <svg class="tube-swoosh" viewBox="0 0 271 241" preserveAspectRatio="none" aria-hidden="true">
        <path d="M271 0 C 258 120 170 205 0 241 L 271 241 Z" fill="var(--tube-panel)"/>
        <path d="M271 8 C 256 125 168 200 8 236" fill="none" stroke="var(--aqua)" stroke-width="4"/>
      </svg>
      <div class="tube-coral" role="img" aria-label="Illustration of a violet and yellow sea fan coral"></div>
      <div class="tube-volume"><span class="ml">300ml</span><span class="wt">NET WT: 180</span></div>
    </div>
    <div class="tube-cap"></div>
  </section>

  <section class="pouch" aria-label="Ocean Reverie fragrance pouch">
    <div class="pouch-seal"></div>
    <div class="pouch-body">
      <div class="pouch-brand"><span class="brand-dot"></span>TubGlow</div>
      <div class="pouch-fragrance">Ocean Reverie</div>
      <svg class="pouch-rule" viewBox="0 0 260 6" aria-hidden="true">
        <path d="M0 5 Q130 -3 260 5" fill="none" stroke="var(--reef-green)" stroke-width="1.5"/>
      </svg>
      <div class="pouch-scene" role="img" aria-label="Underwater reef illustration with corals, seaweed, stones and a school of fish"></div>
      <svg class="pouch-band" viewBox="0 0 336 130" preserveAspectRatio="none">
        <path d="M0 30 Q170 36 336 0 L336 130 L0 130 Z" fill="var(--pouch-deep)"/>
        <path d="M0 80 Q170 86 336 55 L336 130 L0 130 Z" fill="var(--pouch-navy)" opacity="0.4"/>
        <text x="168" y="66" text-anchor="middle" font-family="Roboto, sans-serif" font-size="14" letter-spacing="2.6" fill="#ffffff" transform="rotate(-5 168 66)">SPA &amp; BATH AROMATHERAPY</text>
      </svg>
      <div class="pouch-volume"><span class="ml">300ml</span>NET WT: 180</div>
    </div>
  </section>

</main>
</body>
</html>
```